Thornvale Group needs a business card design

We need a new business card design using the logo recently selected in a logo competition on Pixel Bazaar. Our business is a consultancy specializing in aviation and energy and the winning business card design will promote an image of precision and professionalism with creativity.

Please use the logo with the name on the front of the card and use a complementary font. Make the back white with either the light grey or dark grey logo.

Target Market(s)

Senior finance and legal leaders at aviation and energy companies

Industry/Entity Type

Management Consulting

Contact Information for Business Card

Peter Castrell
President
Thornvale Group

www.thornvalegroup.example

(555) 204-6391
pc@thornvalegroup.example

Requirements
Must have
• Professional font that goes well with the logo font

```html
<!DOCTYPE html>
<html lang="en">
<head>
<meta charset="utf-8">
<title>Thornvale Group – Business Card</title>
<link rel="stylesheet" href="https://fonts.googleapis.com/css2?family=Open+Sans:wght@400;700&display=swap">
<style>
  :root {
    --navy: #1d4a78;
    --navy-deep: #0b2748;
    --navy-light: #2f6a9c;
    --ink: #1f3f66;
    --grey: #6b6e72;
    --paper: #ffffff;
    --stage: #e9eaec;
    --rule: #2a5a86;
  }
  * { box-sizing: border-box; margin: 0; padding: 0; }
  html, body { width: 1200px; height: 913px; overflow: hidden; }
  body {
    background: var(--stage);
    font-family: "Open Sans", Arial, sans-serif;
    position: relative;
  }
  .card {
    position: absolute;
    width: 525px;
    height: 300px;
    border-radius: 3px;
    overflow: hidden;
    box-shadow: 0 6px 18px rgba(0,0,0,0.18);
  }

  /* Front card */
  .card-front { left: 70px; top: 150px; background: var(--paper); }
  .front-brand {
    position: absolute; right: 36px; top: 58px;
    display: flex; align-items: center; gap: 10px;
  }
  .brand-square { width: 14px; height: 14px; background: var(--navy); }
  .front-brand .brand-name {
    font-size: 22px; font-weight: 400; letter-spacing: 3px;
    color: var(--navy); text-transform: uppercase;
  }
  .front-rule {
    position: absolute; left: 150px; right: 0; top: 112px;
    height: 1px; background: var(--rule);
  }
  .contact-band {
    position: absolute; left: 200px; right: 0; top: 130px; bottom: 0;
    background: linear-gradient(160deg, var(--navy-light), var(--navy-deep));
  }
  .contact-list {
    position: absolute; right: 26px; top: 24px;
    list-style: none; text-align: right;
    color: #fff; font-size: 13px; line-height: 22px;
  }
  .contact-list li { display: flex; justify-content: flex-end; align-items: center; gap: 6px; }
  .contact-list svg { width: 11px; height: 11px; fill: none; stroke: #fff; stroke-width: 1.4; }
  .person { position: absolute; left: 34px; top: 150px; }
  .person-name { font-size: 21px; font-weight: 700; color: var(--ink); }
  .person-title { font-size: 14px; color: var(--grey); margin-top: 1px; }

  /* Back card */
  .card-back {
    left: 605px; top: 460px;
    background: linear-gradient(150deg, #2c6f9f 0%, var(--navy) 45%, var(--navy-deep) 100%);
    display: flex; align-items: center; justify-content: center;
  }
  .back-brand { display: flex; align-items: center; gap: 14px; }
  .back-brand .brand-square { width: 18px; height: 18px; background: #fff; }
  .back-brand .brand-name {
    font-size: 32px; font-weight: 400; letter-spacing: 5px;
    color: #fff; text-transform: uppercase;
  }
</style>
</head>
<body>
  <section class="card card-front" aria-label="Business card front">
    <div class="front-brand">
      <span class="brand-square"></span>
      <span class="brand-name">Thornvale Group</span>
    </div>
    <div class="front-rule"></div>
    <div class="contact-band">
      <ul class="contact-list">
        <li>(555) 204-6391
          <svg viewBox="0 0 12 12"><path d="M3 1l2 2-1 2 3 3 2-1 2 2-2 2C5 11 1 7 1 3z"/></svg></li>
        <li>pc@thornvalegroup.example
          <svg viewBox="0 0 12 12"><rect x="1" y="2.5" width="10" height="7"/><path d="M1 2.5l5 4 5-4"/></svg></li>
        <li>www.thornvalegroup.example
          <svg viewBox="0 0 12 12"><circle cx="6" cy="6" r="5"/><path d="M1 6h10M6 1c3 3 3 7 0 10M6 1c-3 3-3 7 0 10"/></svg></li>
      </ul>
    </div>
    <div class="person">
      <p class="person-name">Peter Castrell</p>
      <p class="person-title">President</p>
    </div>
  </section>

  <section class="card card-back" aria-label="Business card back">
    <div class="back-brand">
      <span class="brand-square"></span>
      <span class="brand-name">Thornvale Group</span>
    </div>
  </section>
</body>
</html>
```